Web Design Project and logo

We need a new web design and logo for www.kz7ventures.com

It is a mobile app development company. Site needs to look very cool/trendy as does the new logo.

Looking for the design (uncoded) and the logo file that my developers can then use to build out the site.

An example of a nice competitor site is www.thecodegarage.com

We want something that looks fresh, clean and hip.

Also development of business cards.

Target Market(s)

Small to mid sized companies

Industry/Entity Type

Business

Requirements
Must have
• Ability to request a quote
Should look very trendy like www.thecodegarage.com as an example of a competitor site

```html
<!DOCTYPE html>
<html lang="en">
<head>
<meta charset="utf-8">
<title>KZ7 Ventures — Mobile App Development</title>
<link rel="stylesheet" href="https://fonts.googleapis.com/css2?family=Arimo:wght@400;700&display=swap">
<style>
  :root{
    --sky-top:#78c5de;
    --sky-bottom:#5aa5bf;
    --hero-light:#c4e6ee;
    --hero-mid:#a9d7e2;
    --content-bg:#e6f4f9;
    --ink:#1c2830;
    --heading:#3b414a;
    --body:#333a40;
    --accent:#e0401c;
    --white:#ffffff;
    --social:#3d6f8c;
    --device-dark:#15181b;
    --device-mid:#3a3f45;
  }
  *{margin:0;padding:0;box-sizing:border-box}
  html,body{width:1200px;height:1000px;overflow:hidden}
  body{
    position:relative;
    font-family:"Arimo",Arial,sans-serif;
    background:linear-gradient(180deg,var(--sky-top) 0%,var(--sky-bottom) 100%);
    color:var(--ink);
  }
  .brand{
    position:absolute;left:48px;top:26px;width:220px;height:115px;
    background:var(--white);border-radius:26px;
    display:flex;align-items:center;justify-content:center;gap:12px;
  }
  .brand-mark{width:22px;height:22px;background:#1f6fb3;border-radius:50%}
  .brand-name{font-size:26px;font-weight:700;color:#1f6fb3;letter-spacing:.5px}
  .main-nav{position:absolute;top:124px;left:0;font-size:15px}
  .main-nav a,.footer-nav a{position:absolute;white-space:nowrap;color:var(--ink);text-decoration:none}
  .social{position:absolute;top:57px;left:1021px;display:flex;gap:16px}
  .social span{width:32px;height:32px;border-radius:5px;background:var(--social);display:block}
  .social span:nth-child(3){background:#e8822c}
  .search{
    position:absolute;left:963px;top:111px;width:189px;height:29px;
    background:var(--white);border-radius:5px;border:1px solid #b9d3dc;
    font-size:18px;color:#8a8f94;padding:8px 0 0 38px;line-height:1;
  }
  .search svg{position:absolute;right:9px;top:4px}
  .hero{
    position:absolute;left:42px;top:170px;width:1116px;height:366px;
    border-radius:30px 30px 0 0;
    background:linear-gradient(90deg,var(--hero-mid) 0%,var(--hero-light) 45%,var(--hero-mid) 100%);
  }
  .hero-title{position:absolute;left:38px;top:153px;font-size:33.5px;font-weight:700;color:#2a2e33;white-space:nowrap}
  .hero-lead{position:absolute;left:38px;top:317px;font-size:21px;color:#3a4046;white-space:nowrap}
  .hero-phones{
    position:absolute;left:530px;top:70px;width:175px;height:222px;border-radius:14px;
    background:linear-gradient(135deg,var(--device-mid) 0%,var(--device-dark) 70%);
  }
  .hero-tablet{
    position:absolute;left:701px;top:30px;width:362px;height:302px;border-radius:14px;
    background:linear-gradient(135deg,var(--device-mid) 0%,var(--device-dark) 60%,#2c3136 100%);
  }
  .content{
    position:absolute;left:42px;top:536px;width:1116px;height:464px;background:var(--content-bg);
  }
  .service{position:absolute;top:64px;width:180px}
  .service h2{font-size:19px;font-weight:700;color:var(--heading);height:33px;white-space:nowrap}
  .service-photo{width:176px;height:134px;margin-bottom:18px}
  .service p{font-size:14.5px;line-height:16px;color:var(--body);white-space:nowrap}
  .service a{display:block;margin-top:8px;font-size:13px;color:var(--accent);text-decoration:none}
  .footer-nav{position:absolute;top:948px;left:0;font-size:13.5px}
</style>
</head>
<body>
  <div class="brand"><span class="brand-mark"></span><span class="brand-name">KZ7 Ventures</span></div>

  <nav class="main-nav">
    <a href="#" style="left:317px">HOME</a>
    <a href="#" style="left:394px">OUR SERVICES</a>
    <a href="#" style="left:552px">A BOUT</a>
    <a href="#" style="left:654px">LATEST NEWS</a>
    <a href="#" style="left:800px">CONTACT US</a>
  </nav>

  <div class="social" aria-label="Social links"><span></span><span></span><span></span></div>

  <div class="search">Search
    <svg width="22" height="22" viewBox="0 0 22 22" aria-hidden="true">
      <circle cx="9" cy="9" r="6" fill="none" stroke="#555" stroke-width="1.6"/>
      <line x1="13.5" y1="13.5" x2="19" y2="19" stroke="#555" stroke-width="2.2" stroke-linecap="round"/>
    </svg>
  </div>

  <section class="hero">
    <h1 class="hero-title">THE NO.1 APP PROVIDER</h1>
    <div class="hero-phones" role="img" aria-label="Two smartphones showing a mobile business app"></div>
    <div class="hero-tablet" role="img" aria-label="Tablet and phone showing a mobile business app"></div>
    <p class="hero-lead">Lorem ipsum dolor sit amet, con sectetuer adipiscing elit. Aenean</p>
  </section>

  <section class="content">
    <article class="service" style="left:99px">
      <h2>MOBILE SERVICES</h2>
      <div class="service-photo" role="img" aria-label="Businessman in a suit using his phone" style="background:linear-gradient(135deg,#e9eef2,#4a5560 60%,#cfd8de)"></div>
      <p>Lorem ipsum dolor sit elit.<br>Aenean commodo de sam</p>
      <a href="#">More</a>
    </article>
    <article class="service" style="left:353px">
      <h2>SUPPORT</h2>
      <div class="service-photo" role="img" aria-label="Team stacking hands together" style="width:174px;background:radial-gradient(circle,#8a6a55 0%,#4a3c36 45%,#f2f2f2 100%)"></div>
      <p>Lorem ipsum dolor sit elit.<br>Aenean commodo de sam</p>
      <a href="#">More</a>
    </article>
    <article class="service" style="left:598px">
      <h2>DEVELOPMENT</h2>
      <div class="service-photo" role="img" aria-label="Developers testing many phones on a desk" style="background:linear-gradient(135deg,#2a2f3a,#5a4a6a 50%,#1c2a3a)"></div>
      <p>Lorem ipsum dolor sit elit.<br>Aenean commodo de sam</p>
      <a href="#">More</a>
    </article>
    <article class="service" style="left:836px;top:64px">
      <h2 style="height:29px">DESIGN</h2>
      <div class="service-photo" role="img" aria-label="Hand holding a phone with floating app icons and clouds" style="width:175px;height:141px;margin-bottom:15px;background:linear-gradient(135deg,#0d2740,#1f6fa8 55%,#0a1a2c)"></div>
      <p>Lorem ipsum dolor sit elit.<br>Aenean commodo de sam</p>
      <a href="#">More</a>
    </article>
  </section>

  <nav class="footer-nav">
    <a href="#" style="left:344px">HOME</a>
    <a href="#" style="left:422px">OUR SERVICES</a>
    <a href="#" style="left:556px">A BOUT</a>
    <a href="#" style="left:635px">LATEST NEWS</a>
    <a href="#" style="left:757px">CONTACT US</a>
  </nav>
</body>
</html>
```